Flat bootstrap design for existing site

I'm looking for a modern flat design based around an existing logo. This has to be a custom design (no external templates), and implemented into a bootstrap framework.

The logo is attached as 2 versions - choose whichever you want, that flows better with whatever design you choose.

Added screenshots of the existing site (currently using the default bootstrap layouts). Please make your designs around those pages in the screenshots (i.e. the homepage only has the postal code input and the header). The active page has 3 screenshots, because I wanted to illustrate the other states that would be visible (in the table rows).

This is a moving/junk removal website, just for some context.

Here's some example websites (flat designs) that I like, just to give you an idea of what I'm after.

https://www.plimvora.com/
https://dacklow.com/
https://trevanu.com/
https://quobrintal.com/en/

Coding

Coded - Design and coding required

Number of Pages Required

5+ page

Colors

Designer to choose colors to be used in the design.

Requirements
Must have
• It must be a modern/simple flat design, that is built around the existing logo (attached).
• It has to be implemented using bootstrap.

```html
<!DOCTYPE html>
<html lang="en">
<head>
<meta charset="utf-8">
<title>Haulbrook – Booking Details</title>
<link href="https://fonts.googleapis.com/css2?family=Montserrat:wght@400;500;600;700&display=swap" rel="stylesheet">
<style>
:root{
  --brand:#4bc8f4;
  --brand-soft:#dcecf5;
  --ink:#1f1f1f;
  --ink-soft:#444;
  --page:#f5f6f8;
  --panel:#f0f1f3;
  --line:#d9dadc;
  --badge:#3a3a3a;
  --footer:#e4e4e6;
}
*{box-sizing:border-box;margin:0;padding:0}
html,body{width:1200px;height:939px;overflow:hidden}
body{font-family:'Montserrat',sans-serif;background:var(--page);color:var(--ink);position:relative}
.top-rule{position:absolute;left:0;top:0;width:1200px;height:3px;background:var(--brand)}
.brand{position:absolute;left:99px;top:36px;display:flex;align-items:center;gap:10px;font-weight:700;font-size:38px;color:var(--brand);letter-spacing:1px}
.brand-dot{width:26px;height:26px;border-radius:50%;background:var(--brand)}
.nav{position:absolute;top:33px;left:570px;display:flex;align-items:center;height:37px;font-size:13.5px;font-weight:500}
.nav a{text-decoration:none;color:var(--ink);padding:0 14px}
.nav a.active{color:var(--brand)}
.nav a.cta{background:var(--brand);color:#fff;height:37px;line-height:37px;padding:0 14px;margin:0 2px}
.nav a.account{padding-left:16px}
.panel{position:absolute;left:99px;width:1003px;background:var(--panel);border:1px solid var(--line)}
.panel-booking{top:108px;height:324px}
.panel-drivers{top:443px;height:324px}
.panel h2{position:absolute;left:56px;top:26px;font-size:17px;font-weight:500;letter-spacing:.2px}
.field-label{position:absolute;font-size:13px;color:var(--ink)}
.field{position:absolute;height:34px;background:#fff;border:1px solid var(--line);font-size:13.5px;padding:0 16px;display:flex;align-items:center;justify-content:space-between}
.textarea{position:absolute;left:57px;top:186px;width:889px;height:69px;background:#fff;border:1px solid var(--line);font-size:13.5px;padding:5px 16px}
.btn-update{position:absolute;left:59px;top:263px;width:76px;height:22px;background:var(--brand);color:#fff;font-size:12px;font-weight:700;text-align:center;line-height:22px}
.notice{position:absolute;left:55px;top:57px;width:875px;height:32px;background:var(--brand-soft);font-size:11.5px;color:#3a5c70;padding-left:10px;line-height:32px}
.table{position:absolute;left:55px;top:101px;width:875px;border:1px solid var(--line);background:#fff}
.row{display:flex;align-items:center;height:36px;border-top:1px solid #e6e6e6;font-size:12px;font-weight:500;position:relative}
.row.head{height:36px;background:var(--brand);color:#fff;font-weight:700;border:none;font-size:11.5px}
.c-name{position:absolute;left:28px}
.head .c-name{left:26px}
.c-dist{position:absolute;left:206px}
.c-time{position:absolute;left:413px}
.row:not(.head) .c-time{left:463px}
.badge{position:absolute;left:592px;background:var(--badge);color:#fff;font-size:12px;font-weight:400;width:69px;height:19px;line-height:19px;text-align:center;border-radius:2px}
.scene{position:absolute;left:237px;top:724px;width:725px;height:167px;background:linear-gradient(90deg,#4bb6e8 0%,#8fb84a 35%,#9a9a9a 65%,#f3b733 100%);opacity:.85}
.footer{position:absolute;left:0;top:891px;width:1200px;height:48px;background:var(--footer)}
.social{position:absolute;left:100px;top:17px;display:flex;gap:20px}
.social span{width:13px;height:13px;border-radius:50%;background:#8a8a8a}
.copy{position:absolute;left:857px;top:19px;font-size:11.5px;color:#333}
</style>
</head>
<body>
<div class="top-rule"></div>
<div class="brand"><span class="brand-dot"></span>Haulbrook</div>
<nav class="nav">
  <a class="active" href="#">BOOK</a>
  <a href="#">HOW IT WORKS</a>
  <a class="cta" href="#">BECOME A DRIVER</a>
  <a class="account" href="#">george@plenwick.com</a>
</nav>

<section class="panel panel-booking">
  <h2>BOOKING DETAILS</h2>
  <label class="field-label" style="left:58px;top:90px">Package Selected:</label>
  <div class="field" style="left:58px;top:108px;width:426px"><span>Package 1</span>
    <svg width="8" height="12" viewBox="0 0 8 12"><path d="M4 0L8 5H0z M4 12L0 7h8z" fill="#666"/></svg></div>
  <label class="field-label" style="left:520px;top:90px">Pick-up time selected:</label>
  <div class="field" style="left:520px;top:108px;width:426px"><span>July 18 at 14:13 am</span>
    <svg width="12" height="12" viewBox="0 0 12 12"><rect x=".5" y="1.5" width="11" height="10" fill="none" stroke="#888"/><rect x=".5" y="1.5" width="11" height="2.5" fill="#888"/><path d="M3 6h2v2H3zM7 6h2v2H7z" fill="#888"/></svg></div>
  <label class="field-label" style="left:58px;top:168px">Description:</label>
  <div class="textarea">1 Large stove</div>
  <div class="btn-update">UPDATE</div>
</section>

<section class="panel panel-drivers">
  <h2>DRIVERS IN YOUR AREA</h2>
  <div class="notice">Please stay on this page and be patient. while we contact the drivers and ind you one ASAP.</div>
  <div class="table">
    <div class="row head"><span class="c-name">Name</span><span class="c-dist">Distance (km)</span><span class="c-time">Agreed Pick-up time</span></div>
    <div class="row"><span class="c-name">Dale Morrow</span><span class="c-dist">4.04km away</span><span class="c-time">-</span><span class="badge">Pending</span></div>
    <div class="row"><span class="c-name">Owen Hartley</span><span class="c-dist">5.7km away</span><span class="c-time">-</span><span class="badge">Pending</span></div>
    <div class="row"><span class="c-name">Felix Brand</span><span class="c-dist">11.13km away</span><span class="c-time">-</span><span class="badge">Pending</span></div>
    <div class="row"><span class="c-name">Rory Pell</span><span class="c-dist">11.91km away</span><span class="c-time">-</span><span class="badge">Pending</span></div>
  </div>
</section>

<div class="scene" role="img" aria-label="Flat illustration of a recycling plant, factory, forklift, rubble piles and a dump truck"></div>

<footer class="footer">
  <div class="social"><span></span><span></span><span></span><span></span></div>
  <div class="copy">Copyrights © 2017 - All Rights Reserved</div>
</footer>
</body>
</html>
```